Dentistry

Dentist's personal business card. No logo needed. The card shoul deliver the massage of reliability, professionalism, experience.
Please ad the full brief of the project: down the line it says: the winning look should be precise and pristine NO pictures of Teeth, smiles, instruments etc.

The details to be desplaid are:
Dr. Rob Tavolen
Doctor of Dental Surgery
PHD
Web. Www.drtavolen.com
Email. Rob@drtavolen.com
Tel 07742318590
Surgery address. 27Bferndale road London SW4 8QT UK
62 Wexley Row London SW3 2HN. Uk

Reason: Decided to make the payment unrefundable in order to get more designers involved.

Requirements
Should not have
• Logo, teeth, smile any sort of instruments.

```html
<!DOCTYPE html>
<html lang="en">
<head>
<meta charset="utf-8">
<title>Dr. Rob Tavolen – Business Card</title>
<link href="https://fonts.googleapis.com/css2?family=Exo+2:wght@400;500;700&display=swap" rel="stylesheet">
<style>
  :root {
    --navy: #1b1546;
    --navy-deep: #15103a;
    --accent: #1f8fe0;
    --ink-light: #ffffff;
    --ink-soft: #c9cbe0;
    --backdrop: #d8dbe1;
  }
  * { margin: 0; padding: 0; box-sizing: border-box; }
  html, body {
    width: 1200px; height: 787px; overflow: hidden;
    background: var(--backdrop);
    font-family: "Exo 2", sans-serif;
  }
  .stage {
    width: 1200px; height: 787px;
    display: flex; align-items: center; justify-content: center; gap: 40px;
  }
  .card {
    position: relative;
    width: 560px; height: 320px;
    background: radial-gradient(ellipse at 50% 40%, var(--navy) 0%, var(--navy-deep) 100%);
    box-shadow: 0 6px 18px rgba(0,0,0,.25);
    color: var(--ink-light);
  }
  /* Front side */
  .card-front .name {
    position: absolute; left: 0; right: 0; top: 118px;
    text-align: center; font-weight: 700; font-size: 30px; letter-spacing: .5px;
  }
  .card-front .degree {
    position: absolute; left: 352px; top: 160px;
    color: var(--accent); font-size: 16px; font-weight: 500;
  }
  .card-front .title-band {
    position: absolute; left: 0; right: 0; top: 200px; height: 34px;
    background: var(--accent);
    display: flex; align-items: center; justify-content: center;
    color: var(--navy); font-size: 18px; font-weight: 500; letter-spacing: 1px;
  }
  /* Back side */
  .icon-rail {
    position: absolute; left: 44px; top: 46px;
    width: 30px; height: 228px; border-radius: 10px;
    background: var(--accent);
  }
  .icon-rail svg { position: absolute; left: 6px; width: 18px; height: 18px; }
  .contact {
    position: absolute; left: 96px; top: 44px; width: 420px;
    font-size: 18px; line-height: 1.45;
  }
  .contact .rule { height: 2px; background: var(--accent); margin: 8px 0 12px; }
  .contact .secondary { color: var(--ink-soft); }
</style>
</head>
<body>
<main class="stage">
  <section class="card card-front">
    <h1 class="name">Dr. Rob Tavolen</h1>
    <p class="degree">PHD</p>
    <p class="title-band">DOCTOR OF DENTAL SURGERY</p>
  </section>

  <section class="card card-back">
    <div class="icon-rail">
      <svg style="top:10px" viewBox="0 0 18 18" fill="none" stroke="#fff" stroke-width="1.6"><circle cx="9" cy="9" r="7.5"/><path d="M6.5 5.5c0 4 2 6.5 5 7l1-1.5-1.8-1-1 .8c-1-.6-1.6-1.4-2-2.6l.9-.9-.8-1.9z" fill="#fff" stroke="none"/></svg>
      <svg style="top:38px" viewBox="0 0 18 18" fill="none" stroke="#fff" stroke-width="1.5"><rect x="2" y="4.5" width="14" height="9" rx="1"/><path d="M2 5l7 5 7-5"/></svg>
      <svg style="top:64px" viewBox="0 0 18 18" fill="none" stroke="#fff" stroke-width="1.4"><circle cx="9" cy="9" r="7"/><ellipse cx="9" cy="9" rx="3" ry="7"/><path d="M2 9h14"/></svg>
      <svg style="top:124px" viewBox="0 0 18 18" fill="none" stroke="#fff" stroke-width="1.6"><path d="M9 16s5-5 5-9a5 5 0 0 0-10 0c0 4 5 9 5 9z"/><circle cx="9" cy="7" r="1.8"/></svg>
    </div>
    <div class="contact">
      <p>07742318590</p>
      <p>Rob@drtavolen.com</p>
      <p>Www.drtavolen.com</p>
      <div class="rule"></div>
      <p>Surgery address:</p>
      <p>27Bferndale road London SW4 8QT UK</p>
      <div class="rule"></div>
      <p class="secondary">62 Wexley Row London SW3 2HN. Uk</p>
    </div>
  </section>
</main>
</body>
</html>
```